Business card design for new eCommerce site focusing on integrity and strong businsess tactics

We need a business card that will stand out and be memorable. Something with color that matches our company logo colors. Think high end version of Pactivo. There are 2 logos provided. The parent company is called Amber Ledge Partners and we are presenting a new and very exciting eCommerce site called BrightHarborTrade.example.

Target Market(s)

Our target markets are in the Activities, Food and Beverage, Health and Beauty

Industry/Entity Type

Marketing

Contact Information for Business Card

We have 4 members that need cards...I will provide all info to the winner of the design contest
Business Address is
4870 West 63rd Avenue, Suite C207
Phoenix AZ 85731

Font styles to use
Serif
Sans Serif

Colors

Designer to choose colors to be used in the design.

Requirements
Must have
• The card must be memorable...should be unique in design but must exude integrity and be playful .
• I have provided several colors or our parent company...please feel free to use which ever
Nice to have
• I will leave this up to you. Feel free to use other images of your choosing that wraps around our client.....Activities, Dining, Health, Beauty
Should not have
• just dont be boring

```html
<!DOCTYPE html>
<html lang="en">
<head>
<meta charset="utf-8">
<title>BrightHarborTrade.example – Business Card</title>
<link rel="stylesheet" href="https://fonts.googleapis.com/css2?family=Source+Sans+3:wght@400;600;700&family=Arimo:wght@400;700&display=swap">
<style>
  :root {
    --brand-blue: #2b7db1;
    --brand-green: #76bd3a;
    --ink-grey: #5a5a5a;
    --paper: #ffffff;
    --backdrop: #ece9e6;
  }
  * { margin: 0; padding: 0; box-sizing: border-box; }
  html, body { width: 1200px; height: 900px; overflow: hidden; }
  body {
    background: var(--backdrop);
    position: relative;
    font-family: "Source Sans 3", "Myriad Pro", sans-serif;
  }
  .card {
    position: absolute;
    overflow: hidden;
    box-shadow: 0 6px 18px rgba(0,0,0,0.18);
  }

  /* Front */
  .card-front {
    left: 177px; top: 74px; width: 589px; height: 364px;
    background: var(--paper);
  }
  .card-front .bands { position: absolute; inset: 0; }
  .brand-lockup {
    position: absolute; left: 128px; top: 62px;
    display: flex; align-items: center; gap: 12px;
  }
  .brand-mark {
    width: 40px; height: 40px; border-radius: 50%;
    background: var(--brand-blue);
  }
  .brand-text { display: flex; flex-direction: column; }
  .brand-name {
    font-size: 23px; font-weight: 600; color: var(--brand-green);
    line-height: 1;
  }
  .brand-tagline {
    margin-top: 6px; font-size: 14px; letter-spacing: 1px;
    color: var(--ink-grey);
  }
  .holder {
    position: absolute; right: 325px; top: 256px; text-align: right;
    color: var(--paper);
  }
  .holder-name { font-size: 20px; font-weight: 600; line-height: 1.1; }
  .holder-title { font-size: 16px; }
  .contact-list {
    position: absolute; left: 291px; top: 246px; list-style: none;
    color: var(--paper); font-size: 16px;
  }
  .contact-list li { display: flex; align-items: center; gap: 8px; height: 21px; }
  .contact-list svg { width: 11px; height: 11px; flex: none; }
  .address {
    position: absolute; left: 0; right: 0; top: 318px; text-align: center;
    color: var(--paper); font-size: 16px;
  }

  /* Back */
  .card-back {
    left: 388px; top: 505px; width: 567px; height: 352px;
    background: var(--brand-blue);
    color: var(--paper); text-align: center;
    font-family: "Arimo", "Helvetica Neue", sans-serif;
  }
  .parent-mark {
    position: absolute; left: 253px; top: 80px;
    width: 62px; height: 62px; border-radius: 50%;
    border: 3px solid var(--paper);
  }
  .parent-name {
    position: absolute; left: 0; right: 0; top: 220px;
    font-size: 32px; font-weight: 700; letter-spacing: 0.5px;
  }
  .parent-web {
    position: absolute; left: 0; right: 0; top: 296px;
    font-size: 17px; letter-spacing: 0.5px;
  }
</style>
</head>
<body>

<section class="card card-front" aria-label="Card front">
  <svg class="bands" width="589" height="364" viewBox="0 0 589 364">
    <polygon points="0,188 404,188 382,214 0,214" fill="var(--brand-green)"/>
    <polygon points="0,218 386,218 419,181 589,181 589,364 0,364" fill="var(--brand-blue)"/>
  </svg>

  <div class="brand-lockup">
    <span class="brand-mark"></span>
    <div class="brand-text">
      <span class="brand-name">BrightHarborTrade.example</span>
      <span class="brand-tagline">Activities-Dining-Health-Beauty</span>
    </div>
  </div>

  <div class="holder">
    <div class="holder-name">DANA WHITFIELD</div>
    <div class="holder-title">Managing Director</div>
  </div>

  <ul class="contact-list">
    <li>
      <svg viewBox="0 0 12 12"><path d="M2.5 1 L4.5 1 L5.2 3.6 L4 4.5 Q5 6.8 7.5 8 L8.4 6.8 L11 7.5 L11 9.5 Q10 11 8.5 11 Q1 9 1 2.5 Q1 1 2.5 1Z" fill="currentColor"/></svg>
      044-555 018 342
    </li>
    <li>
      <svg viewBox="0 0 12 12"><rect x="1" y="2.5" width="10" height="7" fill="currentColor"/><polyline points="1,2.5 6,6.5 11,2.5" fill="none" stroke="var(--brand-blue)" stroke-width="1"/></svg>
      info@brightharbor.example
    </li>
    <li>
      <svg viewBox="0 0 12 12"><circle cx="6" cy="6" r="5" fill="none" stroke="currentColor" stroke-width="1.2"/><ellipse cx="6" cy="6" rx="2.2" ry="5" fill="none" stroke="currentColor" stroke-width="1"/><line x1="1" y1="6" x2="11" y2="6" stroke="currentColor" stroke-width="1"/></svg>
      www.brightharbor.example
    </li>
  </ul>

  <p class="address">4870 West 63rd Avenue, Suite C207 Phoenix AZ 85731</p>
</section>

<section class="card card-back" aria-label="Card back">
  <span class="parent-mark"></span>
  <p class="parent-name">Amber Ledge Partners</p>
  <p class="parent-web">www.amberledge.example</p>
</section>

</body>
</html>
```